RESIDENTIAL CONSTRUCTION

We are a company that specializes in building custom residential homes, the design should also emphasize that quality and service is our priority.

Industry/Entity Type

Construction Company

Contact Information for Business Card

Contact Person: Marcus Lindqvist
Company Address: 273 West Alder Ave San Jose , Ca 95380
Phone Number : 408-731-2946
Email Address: Stoneridgehomes517@mailvista.net

Font styles to use
Sans Serif

Colors
ec1f27

Requirements
Must have
• CSLB # 7362015
Nice to have
• needs to have same color as logo i uploaded, we will be printing these on a clear plastic card.

```html
<!DOCTYPE html>
<html lang="en">
<head>
<meta charset="utf-8">
<title>Stoneridge Homes – Business Card</title>
<link rel="stylesheet" href="https://fonts.googleapis.com/css2?family=Oswald:wght@500&family=Arimo:wght@400&display=swap">
<style>
  :root {
    --page-bg: #e9e6e2;
    --card-frost: #f4f2ef;
    --band-black: #121212;
    --brand-red: #a3161c;
    --brand-red-dark: #6e0d12;
    --logo-red: #9b1117;
    --name-ink: #e4e0d8;
    --contact-ink: #f0e4dc;
    --icon-ink: #f3e6e0;
    --license-ink: #2a2a2a;
  }
  html, body {
    margin: 0;
    padding: 0;
    width: 1200px;
    height: 970px;
    overflow: hidden;
    background: var(--page-bg);
  }
  .business-card {
    position: absolute;
    left: 100px;
    top: 201px;
    width: 1000px;
    height: 568px;
    border-radius: 26px;
    overflow: hidden;
    background: linear-gradient(160deg, #faf9f7 0%, var(--card-frost) 55%, #e8e5e1 100%);
    box-shadow: 0 12px 40px rgba(0,0,0,0.18);
  }
  .card-bands {
    position: absolute;
    inset: 0;
  }
  .brand-lockup {
    position: absolute;
    left: 58px;
    top: 96px;
  }
  .brand-row {
    display: flex;
    align-items: center;
    gap: 16px;
  }
  .brand-mark {
    width: 56px;
    height: 56px;
    background: var(--logo-red);
  }
  .brand-name {
    font-family: "Oswald", sans-serif;
    font-weight: 500;
    font-size: 72px;
    line-height: 1;
    color: var(--logo-red);
    letter-spacing: 0.5px;
  }
  .license {
    margin: 14px 0 0 72px;
    font-family: "Arimo", sans-serif;
    font-size: 22px;
    letter-spacing: 3px;
    color: var(--license-ink);
  }
  .contact-name {
    position: absolute;
    left: 58px;
    top: 326px;
    font-family: "Oswald", sans-serif;
    font-weight: 500;
    font-size: 34px;
    letter-spacing: 0.5px;
    color: var(--name-ink);
    text-transform: uppercase;
  }
  .contact-list {
    position: absolute;
    left: 58px;
    top: 454px;
    margin: 0;
    padding: 0;
    list-style: none;
    font-family: "Arimo", sans-serif;
    font-size: 25px;
    color: var(--contact-ink);
  }
  .contact-list li {
    display: flex;
    align-items: center;
    gap: 14px;
    height: 37px;
  }
  .contact-icon {
    width: 30px;
    height: 30px;
  }
  .address {
    position: absolute;
    right: 64px;
    top: 454px;
    font-family: "Arimo", sans-serif;
    font-size: 25px;
    line-height: 37px;
    color: var(--contact-ink);
    text-align: right;
  }
</style>
</head>
<body>
  <div class="business-card">
    <svg class="card-bands" viewBox="0 0 1000 568" width="1000" height="568">
      <defs>
        <linearGradient id="red-sheen" x1="0" y1="0" x2="1" y2="1">
          <stop offset="0" stop-color="#b3232a"/>
          <stop offset="0.55" stop-color="#8f1218"/>
          <stop offset="1" stop-color="#6e0d12"/>
        </linearGradient>
      </defs>
      <path d="M0 303 H1000 V346 H520 C495 346 495 394 470 394 H0 Z" fill="var(--band-black)"/>
      <path d="M0 394 H470 C495 394 495 346 520 346 H1000 V568 H0 Z" fill="url(#red-sheen)"/>
      <path d="M0 394 H470 C495 394 495 346 520 346 H1000" fill="none" stroke="#d9cfc6" stroke-width="2" opacity="0.7"/>
    </svg>

    <div class="brand-lockup">
      <div class="brand-row">
        <div class="brand-mark"></div>
        <div class="brand-name">STONERIDGE HOMES</div>
      </div>
      <div class="license">CSLB # 7362015</div>
    </div>

    <div class="contact-name">Marcus Lindqvist</div>

    <ul class="contact-list">
      <li>
        <svg class="contact-icon" viewBox="0 0 30 30" aria-hidden="true">
          <circle cx="15" cy="15" r="15" fill="var(--icon-ink)"/>
          <path d="M8 12 C8 9 22 9 22 12 L20 14 L17 12.5 V11.5 H13 V12.5 L10 14 Z M10 15 H20 L21 21 H9 Z" fill="var(--brand-red)"/>
          <circle cx="15" cy="18" r="2" fill="var(--icon-ink)"/>
        </svg>
        <span>408-731-2946</span>
      </li>
      <li>
        <svg class="contact-icon" viewBox="0 0 30 30" aria-hidden="true">
          <circle cx="15" cy="15" r="15" fill="var(--icon-ink)"/>
          <rect x="8" y="10" width="14" height="10" fill="var(--brand-red)"/>
          <path d="M8 10 L15 16 L22 10" fill="none" stroke="var(--icon-ink)" stroke-width="1.5"/>
        </svg>
        <span>Stoneridgehomes517@mailvista.net</span>
      </li>
    </ul>

    <div class="address">
      <div>273 West Alder Ave</div>
      <div>San Jose, Ca 95380</div>
    </div>
  </div>
</body>
</html>
```